Im want a website LIKE VRX's and FleetHollow.com's with product payment options like Trenzo's

I need a website LIKE VRX with a header made EXACTLY LIKE THAT OF FLEETHOLLOWS .

The front page photo should be like that of FLEETHOLLOW's webpage as well.

The name of the website will be called "M.K. (Caldera Key)".

We will be targeting ALL MARKETS in a small town in central Panama and charging businesses "listing fees" like a phone book does but also providing informational blogs, news, and other interesting activities.

THIS IS A MULTI PAGE WEBSITE

THIS IS WHERE VRX's website meets Brivelle/FleetHollow.

Once the layout is built I will tweak and modify, add information, and upload items for sale.

Here is a list of specific categories that should be listed out above the front page header image/search bar

-- Home -- News -- Travel -- Activities -- Shop & Dine -- Store -- More... --

These categories should be spread across the bottom of the page in three sections:

WHATS SO GREAT ABOUT (Caldera Key),
HAND PICKED TOURS
ACTIVITIES etc.

Also lets use www.Trenzo.example 's
"HOT DESTINATIONS"
"BEAT THE BEST PRICES IN CALDERA"
"OCTOBERS INSIDER PICKS"
"TOP DESTINATIONS"
and spread them in four sections side-by-side near the bottom of the page.

Overall I would like to see the finished product to be something LIKE VRX's and FleetHollows.

WE NEED ONLINE PAYMENT OPTIONS LIKE BRIVELLE'S WEBSITE HAS

This will be a desktop website but should be very mobile friendly as well.

-rodmund

P.S. Good luck!

If it isn't already too late to change the website name, the name of the website should be "Caldera Key". Added Friday, October 9, 2015

What do you guys think the budget should be to win this? Added Saturday, October 10, 2015

www.palmorra.example is the most amazing simple site. Whoever can make me a replica with my specifications will win immediately!!!! Added Sunday, October 18, 2015

OMG www.palmorra.example is the bomb!So simple and elegant. Whoever can make me an EXACT REPLICA OF WWW.PALMORRA.EXAMPLE as my site with the specifications mentioned in my brief will take home the $825.00 immediately! Good luck amigos! Added Sunday, October 18, 2015

Does anybody know how to add recurring monthly billing options on this website? Added Sunday, October 18, 2015

ALL MARKETS

Product

Coded - Design and coding required

5+ page

• Coinvey payment options.
• I must be able to add and remove photos/text and video from the HTML files in the page.
• Be creative my friends, and may the odds be forever in your favor!
• I added some photos of a good layout for our page below.

```html
<!DOCTYPE html>
<html lang="en">
<head>
<meta charset="utf-8">
<title>Caldera Source — Activities</title>
<link href="https://fonts.googleapis.com/css2?family=Roboto:ital,wght@0,300;0,400;0,500;0,700;1,400&display=swap" rel="stylesheet">
<style>
:root{
  --orange:#f6b133;
  --orange-deep:#e9a21f;
  --dark:#1f1f1f;
  --darker:#161616;
  --bar:#2a2a2a;
  --ink:#2b2b2b;
  --muted:#8a8a8a;
  --line:#cfcfcf;
  --link:#4aa3e0;
  --white:#fff;
}
*{margin:0;padding:0;box-sizing:border-box}
html,body{width:769px;height:1200px;overflow:hidden;background:#fff}
body{font-family:'Roboto',sans-serif;color:var(--ink);position:relative}
.abs{position:absolute}

/* hero + header */
.hero{left:0;top:0;width:769px;height:162px;background:linear-gradient(180deg,#3c4a2c 0%,#6f6a3c 45%,#8a6a35 75%,#4a3a22 100%)}
.topbar{left:0;top:0;width:769px;height:24px;background:rgba(20,20,20,.55)}
.topbar .contact{top:6px;font-size:8px;color:#fff;display:flex;align-items:center;gap:5px}
.auth{right:60px;top:6px;font-size:8px;font-weight:700;color:#fff;display:flex;gap:5px;align-items:center}
.auth .login{color:var(--orange)}
.mainnav{left:0;top:24px;width:769px;height:19px;background:rgba(20,20,20,.9)}
.mainnav ul{list-style:none;display:flex;position:absolute;left:151px;top:0;height:19px}
.mainnav li{font-size:8px;color:#fff;padding:0 11.5px;line-height:19px}
.mainnav li.active{background:var(--orange-deep)}
.cart{left:657px;top:24px;width:49px;height:18px;background:var(--orange);font-size:7.5px;font-weight:700;color:#222;display:flex;align-items:center;justify-content:center;gap:3px}
.subnav{left:0;top:43px;width:769px;height:19px;background:rgba(255,255,255,.92)}
.subnav ul{list-style:none;display:flex;position:absolute;left:151px;height:19px}
.subnav li{font-size:7.5px;color:#333;padding:0 0 0 11px;width:71px;line-height:19px}
.logo{left:64px;top:0;width:87px;height:67px;background:var(--orange);display:flex;flex-direction:column;align-items:center;justify-content:flex-end;padding-bottom:6px}
.logo .mark{width:30px;height:30px;background:#fff;margin-bottom:6px}
.logo .name{font-size:8px;color:#3a2a10;font-weight:500}
.page-title{left:64px;top:92px;font-size:27px;color:#fff;font-weight:400;letter-spacing:.5px}

.news{left:0;top:162px;width:769px;height:40px;background:var(--dark)}
.news h3{position:absolute;left:64px;top:9px;font-size:20px;font-weight:400;color:#fff;letter-spacing:.5px}
.news .ticker{position:absolute;left:132px;top:8px;width:574px;height:25px;background:#f4f4f4;border:1px solid var(--orange);font-size:7.3px;color:#333;line-height:23px;padding-left:16px}

/* slider */
.slider-zone{left:0;top:202px;width:769px;height:368px;background:radial-gradient(ellipse at 50% 40%,#f8f8f8 0%,#e6e6e6 60%,#d2d2d2 100%)}
.slide-card{left:82px;top:241px;width:604px;height:234px;background:#fff;box-shadow:0 10px 16px rgba(0,0,0,.25)}
.slide-img{left:117px;top:241px;width:535px;height:234px;background:linear-gradient(180deg,#c9d6df 0%,#6b8c8f 35%,#3f6b4e 60%,#55603f 100%)}
.caption{left:117px;top:411px;width:535px;height:64px;background:rgba(15,15,15,.82);padding:9px 11px}
.caption h4{font-size:13px;color:#fff;font-weight:500;margin-bottom:6px}
.caption p{font-size:7.3px;color:#ddd;line-height:10px}
.arrow{top:348px}
.thumbs{left:276px;top:504px;display:flex;gap:1px}
.thumbs span{width:26px;height:24px;border:2px solid #fff;background:linear-gradient(180deg,#8fc0e0,#5a8f4a);box-shadow:0 1px 2px rgba(0,0,0,.3);margin-right:0.4px}
.tip{left:346px;top:486px;background:#111;color:#fff;font-size:5.5px;padding:3px 9px}

/* videos */
.accent{left:64px;top:600px;width:55px;height:4px;background:var(--orange)}
.section-h{left:64px;top:614px;font-size:21px;font-weight:400;color:#333}
.rule{left:260px;top:623px;width:446px;height:5px;background:#cfcfcf}
.video{top:657px;width:205px}
.video .pic{height:93px}
.video .strip{height:24px;background:var(--orange);font-size:7px;color:#fff;display:flex;align-items:center;gap:5px;padding-left:8px}
.video .title{margin-top:9px;height:21px;background:#1c1c1c;color:#fff;font-size:11px;font-weight:300;line-height:21px;padding-left:8px}
.play{left:0;top:0;width:205px;height:117px;display:flex;flex-direction:column;align-items:center;justify-content:center;color:#fff;font-size:8px;gap:2px}

/* newsletter */
.newsletter{left:0;top:836px;width:769px;height:145px;background:linear-gradient(180deg,#41535a 0%,#5a6b5f 55%,#6a6150 100%)}
.nl-title{left:0;top:854px;width:769px;text-align:center;font-size:20px;color:#fff;font-weight:500}
.nl-sub{left:0;top:883px;width:769px;text-align:center;font-size:10px;color:#fff}
.nl-line{top:867px;height:1px;background:rgba(255,255,255,.5)}
.field{top:916px;height:30px;background:#fff;border:1px solid #ccc;font-size:7.5px;font-style:italic;color:#555;line-height:28px;padding-left:12px}
.subscribe{left:539px;top:916px;width:166px;height:30px;background:var(--orange);color:#222;font-size:12px;letter-spacing:1px;text-align:center;line-height:30px}

/* footer */
.footer{left:0;top:981px;width:769px;height:189px;background:var(--dark)}
.f-logo{left:77px;top:1030px;width:42px;height:38px;background:#fff}
.f-name{left:67px;top:1074px;font-size:8.5px;color:#9a6e2c}
.f-about{left:64px;top:1087px;width:145px;font-size:7px;line-height:12.8px;color:#6d6d6d}
.vsep{top:1025px;width:1px;height:112px;background:#333}
.f-h{top:1023px;font-size:7.5px;font-weight:700;color:#fff}
.social{left:238px;width:73px;height:15px;border-radius:2px;font-size:7.5px;color:#fff;display:flex;align-items:center;padding-left:8px;gap:6px}
.social i{width:5px;height:5px;background:#fff;border-radius:50%;display:block}
.f-list{list-style:none;font-size:7.3px;color:#777}
.f-list li{height:18.7px}
.tweet{left:562px;font-size:6.8px;color:#ddd;line-height:8.6px}
.tweet b{color:#fff}
.tweet a{color:var(--link);text-decoration:none}
.bottom{left:0;top:1170px;width:769px;height:30px;background:var(--darker);font-size:7.3px;font-weight:700;color:#fff}
.bottom span{position:absolute;top:11px}
</style>
</head>
<body>

<div class="abs hero" role="img" aria-label="Tropical garden with palm trees and airboats under warm evening light"></div>
<div class="abs topbar">
  <div class="abs contact" style="left:163px">
    <svg width="12" height="9" viewBox="0 0 12 9"><rect x=".5" y=".5" width="11" height="8" fill="none" stroke="#fff"/><path d="M.5 .5 6 5 11.5 .5" fill="none" stroke="#fff"/></svg>
    <span style="margin-left:15px">hello@calderasource.example</span>
  </div>
  <div class="abs contact" style="left:314px">
    <svg width="10" height="10" viewBox="0 0 10 10"><path d="M2 0 4 3 3 4.5Q4.5 6.5 6 7L7 6 10 8 8.5 10Q3 9.5 0 2Z" fill="#fff"/></svg>
    <span>1800-555-0142</span>
  </div>
  <div class="abs auth">
    <svg width="11" height="11" viewBox="0 0 11 11"><path d="M4 1H10V10H4" fill="none" stroke="#fff"/><path d="M0 5.5H7M5 3.5 7 5.5 5 7.5" fill="none" stroke="#fff"/></svg>
    <span class="login" style="margin-left:4px">Login</span><span>/</span><span>Sign Up</span>
  </div>
</div>
<nav class="abs mainnav">
  <ul>
    <li class="active">Home</li><li>Store</li><li>News</li><li>Activities</li><li>Travel</li><li>Shop &amp; Dine</li><li>More</li><li>Contact</li>
  </ul>
</nav>
<div class="abs cart">
  <svg width="11" height="9" viewBox="0 0 11 9"><path d="M0 1H2L3.5 6H9.5L10.5 2.5H3" fill="none" stroke="#222"/><circle cx="4" cy="8" r="1" fill="#222"/><circle cx="9" cy="8" r="1" fill="#222"/></svg>
  CART
</div>
<nav class="abs subnav">
  <ul><li>Home Page 1</li><li>Home Page 2</li><li>Home Page 3</li><li>Home Page 4</li><li>Home Page 5</li></ul>
</nav>
<div class="abs logo"><span class="mark"></span><span class="name">Caldera Source</span></div>
<h1 class="abs page-title">Activities</h1>

<section class="abs news">
  <h3>NEWS:</h3>
  <div class="ticker">The latest travel news on the most significant developments in the travel industry including news affecting travel agents, tour operators,</div>
</section>

<section class="abs slider-zone"></section>
<div class="abs slide-card"></div>
<div class="abs slide-img" role="img" aria-label="Hikers with backpacks resting on a rock above a misty green valley"></div>
<div class="abs caption">
  <h4>Lorem Ipsum Is Simply Dummy Text</h4>
  <p>Nullam pretium auctor massa ut consequat. Etiam hendrerit iaculis mattis. Proin tincidunt gravida augue in tempor. Proin blandit, elit a consectetur tincidunt, velit quam tristique risus, eget ultrices lorem dui ut nisl.</p>
</div>
<svg class="abs arrow" style="left:93px" width="12" height="20" viewBox="0 0 12 20"><path d="M10 2 2 10 10 18" fill="none" stroke="#333" stroke-width="2.5"/></svg>
<svg class="abs arrow" style="left:662px" width="12" height="20" viewBox="0 0 12 20"><path d="M2 2 10 10 2 18" fill="none" stroke="#333" stroke-width="2.5"/></svg>
<div class="abs tip">Lorem ipsum</div>
<div class="abs thumbs" role="img" aria-label="Thumbnail strip of beach and city photos">
  <span></span><span></span><span></span><span></span><span></span><span></span><span></span><span></span>
</div>

<div class="abs accent"></div>
<h2 class="abs section-h">Must Watch Videos</h2>
<div class="abs rule"></div>

<article class="abs video" style="left:64px">
  <div class="pic" role="img" aria-label="Family picnic beside a car with camping chairs" style="background:linear-gradient(180deg,#7f8d82,#5b5a4a)"></div>
  <div class="strip"><svg width="9" height="9" viewBox="0 0 9 9"><circle cx="4.5" cy="4.5" r="4" fill="none" stroke="#fff"/><path d="M3.5 2.8 6 4.5 3.5 6.2Z" fill="#fff"/></svg>1:45</div>
  <div class="title">Lorem ipsum is simply dummy text</div>
</article>
<article class="abs video" style="left:283px">
  <div role="img" aria-label="Palm trees on a beach at dusk" style="height:117px;background:linear-gradient(180deg,#2d5a5c,#3f5f55 60%,#8b8a78);border-bottom:2px solid var(--orange)"></div>
  <div class="abs play"><svg width="22" height="22" viewBox="0 0 22 22"><circle cx="11" cy="11" r="9.5" fill="none" stroke="#fff" stroke-width="1.5"/><path d="M9 6.5 15 11 9 15.5Z" fill="#fff"/></svg>PLAY</div>
  <div class="title">Lorem ipsum is simply dummy text</div>
</article>
<article class="abs video" style="left:502px">
  <div class="pic" role="img" aria-label="Ancient stone temple with visitors in a tuk-tuk" style="background:linear-gradient(180deg,#e6ecef,#8a8070 50%,#5a6a40)"></div>
  <div class="strip"><svg width="9" height="9" viewBox="0 0 9 9"><circle cx="4.5" cy="4.5" r="4" fill="none" stroke="#fff"/><path d="M3.5 2.8 6 4.5 3.5 6.2Z" fill="#fff"/></svg>3:52</div>
  <div class="title">Lorem ipsum is simply dummy text</div>
</article>

<section class="abs newsletter" role="img" aria-label="Hikers overlooking a misty valley, darkened backdrop"></section>
<div class="abs nl-line" style="left:64px;width:174px"></div>
<div class="abs nl-line" style="left:509px;width:197px"></div>
<h2 class="abs nl-title">Email Newsletter</h2>
<p class="abs nl-sub">Join our newsletter and get the latest and hottest Hawaii travel deals.</p>
<div class="abs field" style="left:64px;width:220px">Email</div>
<div class="abs field" style="left:297px;width:221px">Zip Code</div>
<div class="abs subscribe">Subscribe</div>

<footer class="abs footer"></footer>
<div class="abs f-logo"></div>
<div class="abs f-name">Caldera Source</div>
<p class="abs f-about">Lorem Ipsum is simply dummy text of the printing and typesetting industry. Lorem Ipsum has been the industry's standard dummy text ever since the 1500.</p>
<div class="abs vsep" style="left:224px"></div>
<div class="abs vsep" style="left:329px"></div>
<div class="abs vsep" style="left:553px"></div>

<h4 class="abs f-h" style="left:238px">FOLLOW US</h4>
<div class="abs social" style="top:1041px;background:#3b5a9a"><i></i>Facepage</div>
<div class="abs social" style="top:1061px;background:#1da7e0"><i></i>Chirper</div>
<div class="abs social" style="top:1081px;background:#d9402f"><i></i>Searchly +</div>
<div class="abs social" style="top:1101px;background:#cc2127"><i></i>Pinboardy</div>

<h4 class="abs f-h" style="left:345px">BEST TOURS</h4>
<ul class="abs f-list" style="left:345px;top:1044px">
  <li>Camping holidays</li><li>Self-catering holidays</li><li>Safaris &amp; wildlife</li><li>Activities &amp; Adventures</li><li>Food &amp; wine holidays</li>
</ul>

<h4 class="abs f-h" style="left:445px">POPULAR COUNTRIES</h4>
<ul class="abs f-list" style="left:445px;top:1044px;height:90px">
  <li>France</li><li>Ukraine</li><li>India</li><li>Spain</li><li>Turkey</li>
</ul>
<ul class="abs f-list" style="left:494px;top:1044px">
  <li>Spain</li><li>Turkey</li><li>France</li><li>Ukraine</li><li>India</li>
</ul>

<h4 class="abs f-h" style="left:562px">LATEST TWEETS</h4>
<p class="abs tweet" style="top:1044px"><b>LinaVoss</b> Trip 5 <a>https://lnk.example/r7Qm2</a><br>@linavoss <a>https://lnk.example/p4Vx8</a></p>
<p class="abs tweet" style="top:1073px"><b>LinaVoss</b> Trip 5 <a>https://lnk.example/r7Qm2</a><br>@linavoss <a>https://lnk.example/p4Vx8</a></p>
<p class="abs tweet" style="top:1100px"><b>LinaVoss</b> Trip 5 <a>https://lnk.example/r7Qm2</a><br>@linavoss <a>https://lnk.example/p4Vx8</a></p>
<div class="abs" style="left:562px;top:1123px;width:112px;height:1px;background:#3a3a3a"></div>

<div class="abs bottom">
  <span style="left:64px">COPYRIGHT @ 2015 CALDERA. ALL RIGHTS RESERVED.</span>
  <span style="right:63px">DESIGNED &amp; DEVELOPED BY NORVEL STUDIO</span>
</div>

</body>
</html>
```